TalkHarbor - Language Coaching Services

Sleek, innovative, trendy design for Language Coaching business.

TalkHarbor is a new UK based company that provides Language Coaching services. We offer highly personalized on-line and face to face language courses. We also impart learning techniques workshops based on the latest neuroscience research for second-language acquisition.

Target Market(s)

See attached info

Industry/Entity Type

Consulting

Contact Information for Business Card

TalkHarbor
DaniaKV@talkharbor.co.uk
TalkHarbor.co.uk
London, UK

Font styles to use
Sans Serif

```html
<!DOCTYPE html>
<html lang="en">
<head>
<meta charset="utf-8">
<title>TalkHarbor – Business Card</title>
<link rel="stylesheet" href="https://fonts.googleapis.com/css2?family=Open+Sans:wght@400;600&display=swap">
<style>
  :root {
    --backdrop: #e7e7e7;
    --card: #231f20;
    --brand-blue: #0a8ac4;
    --band-blue: #0685bf;
    --ink-light: #f2f2f2;
  }
  * { box-sizing: border-box; margin: 0; padding: 0; }
  html, body {
    width: 1200px;
    height: 909px;
    overflow: hidden;
    background: var(--backdrop);
    font-family: "Open Sans", Arial, sans-serif;
  }
  .business-card {
    position: absolute;
    left: 180px;
    top: 214px;
    width: 840px;
    height: 480px;
    background: var(--card);
    color: var(--ink-light);
  }
  .brand {
    position: absolute;
    left: 0;
    right: 0;
    top: 47px;
    text-align: center;
  }
  .brand-circle {
    display: block;
    width: 126px;
    height: 126px;
    margin: 0 auto;
    border: 5px solid var(--brand-blue);
    border-radius: 50%;
  }
  .brand-name {
    margin-top: 30px;
    font-size: 44px;
    font-weight: 600;
    letter-spacing: 2px;
    line-height: 1;
    color: var(--brand-blue);
  }
  .contact-item {
    position: absolute;
    top: 292px;
    font-size: 21px;
    letter-spacing: 0.3px;
    white-space: nowrap;
  }
  .contact-item svg {
    display: block;
    width: 22px;
    height: 22px;
    margin: 0 0 12px 6px;
    fill: var(--brand-blue);
  }
  .contact-phone { left: 44px; }
  .contact-email { left: 255px; }
  .contact-web { left: 563px; }
  .address-band {
    position: absolute;
    left: 0;
    right: 0;
    top: 398px;
    height: 50px;
    background: var(--band-blue);
    display: flex;
    align-items: center;
    justify-content: center;
    font-size: 21px;
    letter-spacing: 0.3px;
    color: var(--ink-light);
  }
</style>
</head>
<body>
  <main class="business-card">
    <header class="brand">
      <span class="brand-circle" aria-hidden="true"></span>
      <h1 class="brand-name">TALKHARBOR</h1>
    </header>

    <div class="contact-item contact-phone">
      <svg viewBox="0 0 24 24" aria-hidden="true">
        <path d="M6.6 10.8c1.4 2.8 3.8 5.1 6.6 6.6l2.2-2.2c.3-.3.7-.4 1-.2 1.1.4 2.3.6 3.6.6.6 0 1 .4 1 1V20c0 .6-.4 1-1 1C10.6 21 3 13.4 3 4c0-.6.4-1 1-1h3.5c.6 0 1 .4 1 1 0 1.3.2 2.5.6 3.6.1.3 0 .7-.2 1l-2.3 2.2z"/>
      </svg>
      +44 1632 960118
    </div>

    <div class="contact-item contact-email">
      <svg viewBox="0 0 24 24" aria-hidden="true">
        <path d="M2 5h20v14H2V5zm2 2v.4l8 5.3 8-5.3V7H4zm16 2.8-8 5.3-8-5.3V17h16V9.8z"/>
      </svg>
      daniakv@talkharbor.co.uk
    </div>

    <div class="contact-item contact-web">
      <svg viewBox="0 0 24 24" aria-hidden="true">
        <path d="M12 2a10 10 0 1 0 0 20 10 10 0 0 0 0-20zm6.9 6h-2.9a15.6 15.6 0 0 0-1.4-3.6A8 8 0 0 1 18.9 8zM12 4c.8 1.2 1.5 2.5 1.9 4h-3.8c.4-1.5 1.1-2.8 1.9-4zM4.3 14a8.2 8.2 0 0 1 0-4h3.4a16.5 16.5 0 0 0 0 4H4.3zm.8 2h2.9c.3 1.3.8 2.5 1.4 3.6A8 8 0 0 1 5.1 16zM8 8H5.1a8 8 0 0 1 4.3-3.6C8.8 5.5 8.3 6.7 8 8zm4 12c-.8-1.2-1.5-2.5-1.9-4h3.8c-.4 1.5-1.1 2.8-1.9 4zm2.3-6H9.7a14.7 14.7 0 0 1 0-4h4.6a14.7 14.7 0 0 1 0 4zm.3 5.6c.6-1.1 1.1-2.3 1.4-3.6h2.9a8 8 0 0 1-4.3 3.6zm1.7-5.6a16.5 16.5 0 0 0 0-4h3.4a8.2 8.2 0 0 1 0 4h-3.4z"/>
      </svg>
      www.talkharbor.co.uk
    </div>

    <footer class="address-band">27&nbsp; Harbour Lane, SE1 4QT, London, UK</footer>
  </main>
</body>
</html>
```